FUN, COLORFUL, AND FAMILY CONCERT THAT CALLED BRAMBLEJAM

A fun, colorful and modern poster. The theme this year is green and yellow, but please use other colors such as Neon or new combinations, patterns, cool design pattern or even splashes background. The name of the event is BRAMBLEJAM. I want the Bramblejam name to stand out and the date as well. Make the website name highlighted so other will go to the website and buy tickets to the concert. The date will be July, 11th, 2015. start time will be 4pm. Location at The Lantern Hall @ Halvorsen University. Tickets will be $15 Adults $12 kids under 12 $5 under 5. I will send the old poster to give you a idea, but I want this year poster to be more of an eye catcher. I am still on the hiring process for the 4 bands will have so leave space for that as well. You can use circle or square or patterns for the photos. I like clear colors as well on the background or patterns. BE YOURSELF & CREATE THIS POSTER FROM YOUR HEART <3

Target Market(s)

everyone.

Industry/Entity Type

University

Font styles to use
Serif

Requirements
Must have
• the small bramblejam logo on the bottom corner. Real people having fun in a concert ..please clear picture nothing blurry!
Nice to have
• brighter and white on the letters for Bramblejam. highlight Bramblejam name, date, and the website (make those bigger). You can use circle, splashes, cool patterns for the date.
Should not have
• be boring ... it needs to be fun and an eye catcher

```html
<!DOCTYPE html>
<html lang="en">
<head>
<meta charset="utf-8">
<title>Bramblejam 2015 Poster</title>
<link rel="stylesheet" href="https://fonts.googleapis.com/css2?family=Rubik+Dirt&family=Oswald:wght@500;700&family=Archivo+Black&family=Open+Sans:wght@400;600&display=swap">
<style>
  :root {
    --stripe-orange: #f5ae1c;
    --stripe-tan: #d6a23a;
    --stripe-olive: #e4cf6e;
    --stripe-peach: #fbc6a2;
    --ink: #111;
    --band-white: #fbfaf4;
    --gold-line: #d9b54a;
    --tickets-grey: #555;
    --price-red: #e2531f;
    --swoosh: #eef7a6;
    --date-green: #24330f;
    --footer-white: #fff6df;
    --url-yellow: #ffe25a;
  }
  html, body { margin: 0; padding: 0; overflow: hidden; background: #fff; }
  .poster { display: block; width: 857px; height: 1200px; }
  .photo-label { font-family: "Open Sans", sans-serif; font-weight: 400; fill: #a9a9a9; }
  .band-caption { font-family: "Archivo Black", sans-serif; fill: #fff; letter-spacing: 2px; }
  .tickets { font-family: "Oswald", sans-serif; font-weight: 700; fill: var(--tickets-grey); }
  .tickets .price { fill: var(--price-red); }
  .event-title { font-family: "Rubik Dirt", serif; }
  .event-date { font-family: "Rubik Dirt", serif; fill: var(--date-green); }
  .venue { font-family: "Open Sans", sans-serif; font-weight: 600; fill: var(--date-green); }
  .footer-info { font-family: "Oswald", sans-serif; font-weight: 500; fill: var(--footer-white); letter-spacing: 1px; }
  .footer-info .url { fill: var(--url-yellow); }
  .corner-mark { font-family: "Oswald", sans-serif; font-weight: 700; fill: #3a1a0c; }
</style>
</head>
<body>
<svg class="poster" viewBox="0 0 1000 1400" xmlns="http://www.w3.org/2000/svg">
  <defs>
    <linearGradient id="lower-heat" x1="0" y1="0" x2="0" y2="1">
      <stop offset="0" stop-color="#f08a1c" stop-opacity="0"/>
      <stop offset="0.5" stop-color="#f19420" stop-opacity="0.7"/>
      <stop offset="0.8" stop-color="#e45a18"/>
      <stop offset="1" stop-color="#a4221a"/>
    </linearGradient>
    <linearGradient id="title-fill" x1="0" y1="0" x2="1" y2="0">
      <stop offset="0" stop-color="#4a1d08"/>
      <stop offset="0.3" stop-color="#d8730f"/>
      <stop offset="0.5" stop-color="#ffc21a"/>
      <stop offset="0.75" stop-color="#f08a12"/>
      <stop offset="1" stop-color="#3a1406"/>
    </linearGradient>
    <linearGradient id="crowd-fill" x1="0" y1="0" x2="0" y2="1">
      <stop offset="0" stop-color="#3a1a0a"/>
      <stop offset="1" stop-color="#1d0b04"/>
    </linearGradient>
    <linearGradient id="swoosh-fill" x1="0" y1="0" x2="1" y2="0">
      <stop offset="0" stop-color="#b7d93a"/>
      <stop offset="0.5" stop-color="#eaf59a"/>
      <stop offset="1" stop-color="#fbfdc8"/>
    </linearGradient>
    <linearGradient id="mark-fill" x1="0" y1="0" x2="0" y2="1">
      <stop offset="0" stop-color="#fdf3b8"/>
      <stop offset="1" stop-color="#e9c95a"/>
    </linearGradient>
  </defs>

  <g class="backdrop">
    <rect x="0" y="0" width="232" height="1400" fill="var(--stripe-orange)"/>
    <rect x="232" y="0" width="278" height="1400" fill="var(--stripe-tan)"/>
    <rect x="510" y="0" width="278" height="1400" fill="var(--stripe-olive)"/>
    <rect x="788" y="0" width="212" height="1400" fill="var(--stripe-peach)"/>
    <rect x="0" y="600" width="1000" height="800" fill="url(#lower-heat)"/>
  </g>

  <g class="band-strip" transform="rotate(-17 500 230)">
    <rect x="-120" y="120" width="1240" height="240" fill="var(--ink)"/>
    <g class="band-slot">
      <rect x="-10" y="140" width="225" height="170" fill="#fff"/>
      <text class="photo-label" font-size="38" text-anchor="middle"><tspan x="102" y="200">YOUR</tspan><tspan x="102" y="240">PHOTO</tspan><tspan x="102" y="280">HERE</tspan></text>
      <text class="band-caption" x="102" y="343" font-size="19" text-anchor="middle">YOUR TEXT HERE</text>
    </g>
    <g class="band-slot">
      <rect x="245" y="140" width="225" height="170" fill="#fff"/>
      <text class="photo-label" font-size="38" text-anchor="middle"><tspan x="357" y="200">YOUR</tspan><tspan x="357" y="240">PHOTO</tspan><tspan x="357" y="280">HERE</tspan></text>
      <text class="band-caption" x="357" y="343" font-size="19" text-anchor="middle">YOUR TEXT HERE</text>
    </g>
    <g class="band-slot">
      <rect x="500" y="140" width="225" height="170" fill="#fff"/>
      <text class="photo-label" font-size="38" text-anchor="middle"><tspan x="612" y="200">YOUR</tspan><tspan x="612" y="240">PHOTO</tspan><tspan x="612" y="280">HERE</tspan></text>
      <text class="band-caption" x="612" y="343" font-size="19" text-anchor="middle">YOUR TEXT HERE</text>
    </g>
    <g class="band-slot">
      <rect x="755" y="140" width="225" height="170" fill="#fff"/>
      <text class="photo-label" font-size="38" text-anchor="middle"><tspan x="867" y="200">YOUR</tspan><tspan x="867" y="240">PHOTO</tspan><tspan x="867" y="280">HERE</tspan></text>
      <text class="band-caption" x="867" y="343" font-size="19" text-anchor="middle">YOUR TEXT HERE</text>
    </g>
  </g>

  <g class="title-band" transform="rotate(-15 500 560)">
    <rect x="-150" y="430" width="1300" height="300" fill="var(--band-white)" opacity="0.92"/>
    <rect x="-150" y="505" width="1300" height="3" fill="var(--gold-line)"/>
    <rect x="-150" y="715" width="1300" height="3" fill="var(--gold-line)"/>
    <text class="tickets" x="28" y="490" font-size="30">TICKETS WILL BE  •  <tspan class="price">$15</tspan> ADULTS  •  <tspan class="price">$12</tspan> KIDS UNDER 12  •  <tspan class="price">$5</tspan> UNDER 5</text>
    <text class="event-title" x="30" y="690" font-size="200" textLength="960" lengthAdjust="spacingAndGlyphs" fill="url(#title-fill)">BRAMBLEJAM</text>
  </g>

  <g class="crowd" role="img" aria-label="Photo of a concert crowd cheering with raised hands">
    <path d="M0 880 L40 840 L70 870 L120 830 L160 800 L220 820 L260 780 L320 790 L380 740 L430 760 L480 700 L540 720 L600 660 L660 680 L720 620 L780 640 L840 600 L900 610 L960 580 L1000 590 L1000 860 L0 1090 Z" fill="url(#crowd-fill)"/>
  </g>

  <g class="date-block">
    <path d="M0 1250 C300 1110 650 1010 1000 965 L1000 1020 C650 1070 320 1200 70 1400 L0 1400 Z" fill="url(#swoosh-fill)"/>
    <path d="M150 1400 C380 1270 640 1180 885 1150 L875 1200 C650 1230 450 1310 300 1400 Z" fill="var(--swoosh)"/>
    <text class="event-date" x="105" y="1330" font-size="100" textLength="640" lengthAdjust="spacingAndGlyphs" transform="rotate(-26 105 1330)">JULY 11, 2015</text>
    <text class="venue" x="265" y="1372" font-size="25" textLength="590" lengthAdjust="spacingAndGlyphs" transform="rotate(-17 265 1372)">4PM • The Lantern Hall @ Halvorsen University</text>
  </g>

  <text class="footer-info" x="495" y="1385" font-size="17">•  FOR MORE INFORMATION GO TO: <tspan class="url">BRAMBLEJAMPC.COM</tspan></text>
  <g class="corner-mark-block">
    <rect x="872" y="1286" width="110" height="80" fill="url(#mark-fill)"/>
    <text class="corner-mark" x="927" y="1334" font-size="19" text-anchor="middle">BRAMBLEJAM</text>
  </g>
</svg>
</body>
</html>
```